World leading Water filters German made

I am a local Plumbing business who is authorised water filter installer
I want to do a Flyer design double sided targeting niche market for Water Filters.
My company colours are black background with white writing.
( but happy to go into different colours to capture more people )
I want all my stuff, sleek and professional with the same fonts throughout.
Www.brightpipeandboiler.au
Is my website you can see how I do things there.
I want the local business awards finalist logo on the flyer too ( it’ll be in the photo)
This Flyer I want all about health and wellness making big points on water filtration benefits
Massive to included HYDROGEN WATER AND ALKALINE WATER ,
REMOVE FLUORIDE
I don’t know whether to have it with the pre-save branded information I sent over, but I don’t want the company other companies name everywhere
I want the main focus about my company Bright Pipe And Boiler Experts
I want the focus to be about a family owned and run Illawarra local business establish for over 20 years.
Please note I have included a Customer brochure the company has designed so you can see some key points on the second page about the products. I want this a lot more eye-catching and appealing please
Target Market(s)
Health and wellness people
Colors
Designer to choose colors to be used in the design.
Requirements
Must have
- Call Derek 0459 237 816, my website , social media buttons ,
Nice to have
- World leading , health and wellness ,
Should not have
- Any information to lead them away from calling myself , I’m the authorities dealer for clearspring supply but I want to no have as much anout them.

```html
<!DOCTYPE html>
<html lang="en">
<head>
<meta charset="utf-8">
<title>Bright Pipe And Boiler Experts – Pure Water Flyer, Both Sides</title>
<link rel="stylesheet" href="https://fonts.googleapis.com/css2?family=League+Gothic&family=Montserrat:ital,wght@0,400;0,500;0,600;0,700;0,800;1,500&family=Poppins:wght@300;400&display=swap">
<style>
  :root{
    --brand-blue:#2c6bd2;
    --brand-blue-deep:#2459b8;
    --brand-blue-soft:#b9cdee;
    --ink:#23222a;
    --panel-dark:#2b2a32;
    --paper:#e4e5e9;
    --white:#ffffff;
    --muted:#c9c9d1;
    --stage:#dcdbd3;
  }
  *{box-sizing:border-box;margin:0;padding:0}
  html,body{width:1200px;height:800px;overflow:hidden;background:var(--stage)}
  .canvas{position:relative;width:1200px;height:800px}

  .flyer{
    position:absolute;top:27px;width:675px;height:955px;
    transform:scale(.78);transform-origin:top left;
    background:var(--paper);overflow:hidden;
    box-shadow:0 10px 28px rgba(0,0,0,.18);
    font-family:"Montserrat",sans-serif;color:var(--ink);
  }
  .flyer-back{left:60px}
  .flyer-front{left:614px}
  .flyer-shapes{position:absolute;left:0;top:0}

  .brand-name{
    position:absolute;left:40px;top:44px;width:170px;
    font-weight:800;font-size:17px;line-height:1.15;
    color:var(--white);text-transform:uppercase;letter-spacing:.5px;
  }

  /* front */
  .headline{
    position:absolute;left:36px;top:160px;
    font-family:"League Gothic",sans-serif;font-weight:400;font-size:76px;line-height:58px;
    color:var(--white);text-transform:uppercase;
  }
  .headline span{display:block}
  .headline-sub{
    position:absolute;left:250px;top:286px;width:170px;
    font-family:"Poppins",sans-serif;font-weight:400;font-size:15px;line-height:19px;color:var(--white);
  }
  .award-badge{position:absolute;left:43px;top:362px;width:48px;height:88px;background:#b3242b}
  .why-title{position:absolute;left:38px;top:495px;font-weight:800;font-size:20px}
  .why-title .accent{color:var(--brand-blue)}
  .why-list{position:absolute;left:38px;top:542px;list-style:none}
  .why-list li{
    position:relative;padding-left:36px;height:34px;
    font-weight:700;font-size:17px;text-transform:uppercase;letter-spacing:.2px;
  }
  .why-list li::before{content:"";position:absolute;left:2px;top:6px;width:11px;height:11px;background:var(--brand-blue)}
  .emergency{position:absolute;left:496px;top:590px;display:flex;align-items:center;gap:6px}
  .emergency-number{font-weight:800;font-size:40px;line-height:1}
  .emergency-label{font-style:italic;font-weight:500;font-size:12.5px;line-height:16px;text-transform:uppercase}
  .services-tab{
    position:absolute;left:275px;top:656px;width:124px;text-align:center;
    font-weight:700;font-size:19px;line-height:22px;color:var(--white);white-space:nowrap;
  }
  .service{position:absolute;color:var(--white)}
  .service h3{font-weight:600;font-size:18px;letter-spacing:.4px;margin-bottom:5px;white-space:nowrap}
  .service p{font-family:"Poppins",sans-serif;font-weight:300;font-size:10.5px;line-height:11.5px;color:var(--muted)}

  .footer-band{
    position:absolute;left:0;top:898px;width:675px;height:42px;background:var(--brand-blue);
    display:flex;align-items:center;gap:50px;padding-left:150px;color:var(--white);
    font-weight:700;font-size:16px;
  }
  .footer-band .contact{display:flex;align-items:center;gap:14px;white-space:nowrap}
  .footer-strip{position:absolute;left:140px;top:940px;width:535px;height:15px;background:var(--ink)}

  /* back */
  .back-headline{
    position:absolute;left:40px;top:160px;
    font-family:"League Gothic",sans-serif;font-size:70px;line-height:60px;
    color:var(--white);text-transform:uppercase;
  }
  .back-headline span{display:block;white-space:nowrap}
  .benefits-title{
    position:absolute;left:0;top:510px;width:675px;text-align:center;
    font-weight:800;font-size:22px;text-transform:uppercase;letter-spacing:.5px;
  }
  .benefit{position:absolute;width:255px}
  .benefit h3{font-weight:700;font-size:17px;margin-bottom:5px;white-space:nowrap}
  .benefit p{font-size:10.5px;line-height:13px;font-weight:400;color:#3a3942}
</style>
</head>
<body>
<main class="canvas">

  <!-- back side -->
  <article class="flyer flyer-back">
    <svg class="flyer-shapes" viewBox="0 0 675 955" width="675" height="955">
      <polygon class="hero-blue" points="0,0 675,0 675,395 0,452" fill="var(--brand-blue)"/>
      <polygon class="edge-line" points="330,424 675,395 675,404 330,432" fill="var(--ink)"/>
      <polygon class="chevron" points="0,898 0,862 110,812 400,898" fill="var(--ink)"/>
      <polygon class="chevron-inner" points="0,898 0,884 110,838 320,898" fill="var(--paper)"/>
      <g fill="var(--brand-blue)">
        <polygon points="78,562 98,573 98,597 78,608 58,597 58,573"/>
        <polygon points="78,647 98,658 98,682 78,693 58,682 58,658"/>
        <polygon points="78,732 98,743 98,767 78,778 58,767 58,743"/>
        <polygon points="388,562 408,573 408,597 388,608 368,597 368,573"/>
        <polygon points="388,647 408,658 408,682 388,693 368,682 368,658"/>
        <polygon points="388,732 408,743 408,767 388,778 368,767 368,743"/>
      </g>
      <g fill="none" stroke="var(--white)" stroke-width="2">
        <circle cx="78" cy="585" r="7"/><path d="M73 580 l10 10"/>
        <circle cx="78" cy="670" r="7"/><circle cx="78" cy="670" r="2.5"/>
        <path d="M72 748 q4 5 0 10 M78 748 q4 5 0 10 M84 748 q4 5 0 10 M69 762 h18 l-3 7 h-12z"/>
        <path d="M388 577 q-8 10 0 16 q8-6 0-16z"/>
        <circle cx="388" cy="670" r="8"/><path d="M384 670 h8"/>
        <path d="M381 749 h14 v8 h-7 v8"/>
      </g>
    </svg>

    <div class="brand-name">Bright Pipe<br>And Boiler<br>Experts</div>
    <h1 class="back-headline">
      <span>With 20+ Years</span>
      <span>I'm Your Trusted Plumber</span>
      <span>And Hot Water Specialist</span>
    </h1>

    <h2 class="benefits-title">Our Benefits</h2>
    <div class="benefit" style="left:112px;top:562px">
      <h3>Reduce the Risk of Cancer</h3>
      <p>Safeguarding health through clean water and proper waste disposal, reducing cancer risk one tap at a time</p>
    </div>
    <div class="benefit" style="left:112px;top:647px">
      <h3>Relief for Eczema sufferers</h3>
      <p>Providing relief for eczema sufferers through water filtration and optimal moisture control.</p>
    </div>
    <div class="benefit" style="left:112px;top:732px">
      <h3>Anti-Aging benefits</h3>
      <p>Supporting anti-aging with clean water for hydration and toxin-free environments.</p>
    </div>
    <div class="benefit" style="left:422px;top:562px;width:230px">
      <h3>Hydrogen Rich Water</h3>
      <p>Antioxidant support for energy, recovery and everyday wellbeing.</p>
    </div>
    <div class="benefit" style="left:422px;top:647px;width:230px">
      <h3>Alkaline Balance</h3>
      <p>Balanced pH water that tastes fresh and helps keep you hydrated.</p>
    </div>
    <div class="benefit" style="left:422px;top:732px;width:230px">
      <h3>Fluoride Removal</h3>
      <p>Removing fluoride and chemicals before water reaches your tap.</p>
    </div>

    <footer class="footer-band">
      <span class="contact">
        <svg width="16" height="16" viewBox="0 0 16 16"><path d="M3 1 q-4 6 2 12 q6 5 10 1 l-3-3 q-2 2-4 0 q-3-3-1-5z" fill="var(--white)"/></svg>
        +0459 237 816</span>
      <span class="contact">
        <svg width="16" height="16" viewBox="0 0 16 16" fill="none" stroke="var(--white)" stroke-width="1.4"><circle cx="8" cy="8" r="7"/><ellipse cx="8" cy="8" rx="3" ry="7"/><path d="M1 8 h14 M2.5 4.5 h11 M2.5 11.5 h11"/></svg>
        Visit our website</span>
    </footer>
    <div class="footer-strip"></div>
  </article>

  <!-- front side -->
  <article class="flyer flyer-front">
    <svg class="flyer-shapes" viewBox="0 0 675 955" width="675" height="955">
      <defs>
        <linearGradient id="bathroomTones" x1="0" y1="0" x2="1" y2="1">
          <stop offset="0" stop-color="#d9dde2"/>
          <stop offset=".45" stop-color="#a9583c"/>
          <stop offset="1" stop-color="#4a4540"/>
        </linearGradient>
        <linearGradient id="filterTones" x1="0" y1="0" x2="0" y2="1">
          <stop offset="0" stop-color="#6d6a66"/>
          <stop offset="1" stop-color="#2f2d2b"/>
        </linearGradient>
        <linearGradient id="storeTones" x1="0" y1="0" x2="0" y2="1">
          <stop offset="0" stop-color="#c9473c"/>
          <stop offset="1" stop-color="#b7b3b0"/>
        </linearGradient>
      </defs>
      <polygon class="hero-blue" points="0,0 420,0 330,195 505,348 0,487" fill="var(--brand-blue)"/>
      <polygon class="hero-photo" role="img" aria-label="Modern bathroom with brick wall, round mirrors and stone basin"
               points="418,0 675,0 675,285 540,365 330,195" fill="url(#bathroomTones)"/>
      <polygon class="accent-tile" points="675,305 675,370 620,340" fill="var(--brand-blue-soft)"/>
      <polygon points="425,388 505,434 505,526 425,572 345,526 345,434" fill="var(--brand-blue)"/>
      <polygon role="img" aria-label="Whole-house water filter unit installed"
               points="425,398 497,439 497,521 425,562 353,521 353,439" fill="url(#filterTones)"/>
      <polygon points="597,388 677,434 677,526 597,572 517,526 517,434" fill="var(--brand-blue)"/>
      <polygon role="img" aria-label="Work van shelving stocked with plumbing parts"
               points="597,398 669,439 669,521 597,562 525,521 525,439" fill="url(#storeTones)"/>
      <g class="phone-icon" fill="none" stroke="var(--ink)" stroke-width="2.2">
        <path d="M452 598 q18-10 36 0 v6 h-8 v-4 q-10-4-20 0 v4 h-8z"/>
        <rect x="455" y="608" width="30" height="16" rx="3"/>
        <text x="459" y="620" font-family="Montserrat,sans-serif" font-size="8" font-weight="700" fill="var(--ink)" stroke="none">24/7</text>
      </g>
      <rect class="services-panel" x="37" y="665" width="600" height="213" fill="var(--panel-dark)"/>
      <polygon class="services-tab-shape" points="226,644 462,644 450,689 212,689" fill="var(--brand-blue)"/>
      <g fill="var(--brand-blue)">
        <polygon points="88,708 107,719 107,741 88,752 69,741 69,719"/>
        <polygon points="400,708 419,719 419,741 400,752 381,741 381,719"/>
        <polygon points="88,797 107,808 107,830 88,841 69,830 69,808"/>
        <polygon points="400,797 419,808 419,830 400,841 381,830 381,808"/>
      </g>
      <g fill="none" stroke="var(--white)" stroke-width="2">
        <circle cx="88" cy="730" r="7"/><circle cx="88" cy="730" r="2.5"/>
        <path d="M394 724 v12 h8 M402 730 h8 v12"/>
        <path d="M82 812 q4 5 0 10 M88 812 q4 5 0 10 M94 812 q4 5 0 10 M79 826 h18 l-3 8 h-12z"/>
        <path d="M392 830 v-10 h16 v10 M400 820 v-6 M396 814 h8"/>
      </g>
    </svg>

    <div class="brand-name">Bright Pipe<br>And Boiler<br>Experts</div>
    <h1 class="headline"><span>Pure Water</span><span>Pure Wellness</span><span>Pure Life</span></h1>
    <p class="headline-sub">Discover the Power of Hydrogen and Alkaline Water</p>
    <div class="award-badge" role="img" aria-label="Local business awards finalist badge"></div>

    <h2 class="why-title"><span class="accent">WHY</span> CHOOSE US ?</h2>
    <ul class="why-list">
      <li>Available 24/7</li>
      <li>Fully Licensed &amp; Insured</li>
      <li>Family Run Local Business</li>
    </ul>
    <div class="emergency">
      <span class="emergency-number">24</span>
      <span class="emergency-label">Emergency<br>Services</span>
    </div>

    <h2 class="services-tab" style="left:275px">Our Services</h2>
    <div class="service" style="left:121px;top:710px;width:230px">
      <h3>Hot Water Systems</h3>
      <p>Contact us for hot water solutions<br><br>with our expert plumbing services.</p>
    </div>
    <div class="service" style="left:434px;top:706px;width:195px">
      <h3>Blocked Drains</h3>
      <p>Blocked drains can be a major inconvenience and potential health hazard in any home or business.</p>
    </div>
    <div class="service" style="left:121px;top:798px;width:215px">
      <h3>Hot Water Servicing</h3>
      <p>Hot water servicing is part of our main plumbing services we provide to assure your comfort and safety at home.</p>
    </div>
    <div class="service" style="left:434px;top:801px;width:198px">
      <h3>Gas Plumbing</h3>
      <p>Contact us for all-around gas plumbing services. From installations to routine maintenance and repairs.</p>
    </div>

    <footer class="footer-band">
      <span class="contact">
        <svg width="16" height="16" viewBox="0 0 16 16"><path d="M3 1 q-4 6 2 12 q6 5 10 1 l-3-3 q-2 2-4 0 q-3-3-1-5z" fill="var(--white)"/></svg>
        +0459 237 816</span>
      <span class="contact">
        <svg width="16" height="16" viewBox="0 0 16 16" fill="none" stroke="var(--white)" stroke-width="1.4"><circle cx="8" cy="8" r="7"/><ellipse cx="8" cy="8" rx="3" ry="7"/><path d="M1 8 h14 M2.5 4.5 h11 M2.5 11.5 h11"/></svg>
        Visit our website</span>
    </footer>
    <div class="footer-strip"></div>
  </article>

</main>
</body>
</html>
```